Flyer for the Radiant Harvest Worship Day

I am looking to create a flyer for a one day prayer retreat our church is organizing.
This flyer will be posted on social media, websites and will also be printed so it can be mailed to people.
I am looking for something professional, with good use of our logo and band colors (logo colors).
I am counting on the designer's skill, creativity, art and knowledge of media communication to produce a flyer that will effectively and quickly convey the message we are trying to spread.
CONTENT OF THE FLYER:
Event title: Radiant Harvest Worship Day
Date: Tuesday July 2nd, 2019
Time: 11:00AM - 7:00PM
Belmora Hotel, 4875 Wexley Avenue, Portland, Maine 04102 (Room: Juniper)
Event Key words to highlight what the event is about: Prayer, Sharing the Word, Panel discussion, prophecy, Impartation.
Key phrases:
A one day prayer retreat.
Jesus Chris is Lord
Contact info:
www.tolvex.org
Phone: 207 555 3184
Email: contact@brookhavenfold.org

```html
<!DOCTYPE html>
<html lang="en">
<head>
<meta charset="utf-8">
<title>Radiant Harvest Worship Day</title>
<link href="https://fonts.googleapis.com/css2?family=Bebas+Neue&family=Arimo:wght@400;700&family=Cormorant+Garamond:wght@500&display=swap" rel="stylesheet">
<style>
  :root {
    --navy: #0f3457;
    --orange: #f3941f;
    --white: #ffffff;
    --paper: #ffffff;
    --frame: #555555;
    --wood-dark: #1e130c;
    --wood-mid: #6a3e1e;
    --wood-light: #b0733c;
  }
  * { margin: 0; padding: 0; box-sizing: border-box; }
  html, body { width: 858px; height: 1200px; overflow: hidden; background: var(--paper); }
  .canvas {
    position: relative; width: 858px; height: 1200px;
    background: var(--paper); border: 1px solid var(--frame);
  }
  .flyer { position: absolute; left: 32px; top: 46px; width: 782px; height: 1106px; background: var(--navy); overflow: hidden; }
  .top-band { position: absolute; left: 0; top: 0; width: 782px; height: 33px; background: var(--orange); }
  .hero-photo {
    position: absolute; left: 0; top: 33px; width: 782px; height: 541px;
    background:
      radial-gradient(ellipse at 62% 55%, rgba(176,115,60,0.55) 0%, rgba(106,62,30,0.35) 35%, rgba(30,19,12,0) 70%),
      linear-gradient(180deg, #151a20 0%, #2a1c12 35%, var(--wood-mid) 65%, var(--wood-dark) 100%);
  }
  .logo-box {
    position: absolute; left: 64px; top: 0; width: 204px; height: 204px; background: var(--navy);
    display: flex; align-items: center; justify-content: center;
  }
  .brand-name {
    font-family: "Cormorant Garamond", serif; font-weight: 500; color: var(--white);
    font-size: 46px; letter-spacing: 1px;
  }
  .event-title {
    position: absolute; left: 60px; top: 378px; color: var(--white);
    font-family: "Bebas Neue", sans-serif; font-weight: 400; line-height: 0.92;
  }
  .event-title .line-1 { display: block; font-size: 68px; }
  .event-title .line-2 { display: block; font-size: 92px; }
  .keywords {
    position: absolute; left: 62px; top: 532px; color: var(--white);
    font-family: "Arimo", sans-serif; font-size: 19px; letter-spacing: 0.3px;
  }
  .keywords .dot { color: var(--orange); padding: 0 6px; }
  .tagline-band {
    position: absolute; left: 0; top: 588px; width: 782px; height: 96px; background: var(--orange);
    text-align: center; color: var(--white); font-family: "Arimo", sans-serif; padding-top: 2px; line-height: 1.1;
  }
  .tagline-band .sub { display: block; font-size: 35px; font-weight: 400; }
  .tagline-band .main { display: block; font-size: 51px; font-weight: 700; }
  .details { position: absolute; left: 130px; top: 712px; font-family: "Arimo", sans-serif; color: var(--white); }
  .detail { display: flex; align-items: center; gap: 12px; font-size: 28px; line-height: 1.4; }
  .detail + .detail { margin-top: 24px; }
  .detail svg { flex: none; width: 46px; height: 46px; }
  .footer-rule { position: absolute; left: 30px; top: 990px; width: 720px; height: 1px; background: rgba(255,255,255,0.6); }
  .footer-brand { position: absolute; left: 66px; top: 1010px; }
  .contact { position: absolute; left: 276px; top: 1005px; font-family: "Arimo", sans-serif; color: var(--white); font-size: 31px; }
  .contact-row { display: flex; align-items: center; gap: 10px; height: 40px; }
  .contact-row svg { width: 24px; height: 24px; flex: none; }
</style>
</head>
<body>
<div class="canvas">
  <div class="flyer">
    <div class="top-band"></div>
    <div class="hero-photo" role="img" aria-label="Photo of a person kneeling in prayer among wooden church pews"></div>
    <div class="logo-box"><span class="brand-name">TOLVEX</span></div>

    <h1 class="event-title">
      <span class="line-1">Radiant Harvest</span>
      <span class="line-2">Worship Day</span>
    </h1>

    <p class="keywords">Prayer<span class="dot">•</span>Sharing the Word<span class="dot">•</span>Panel discussion<span class="dot">•</span>Prophecy<span class="dot">•</span>Impartation</p>

    <div class="tagline-band">
      <span class="sub">A ONE DAY PRAYER RETREAT.</span>
      <span class="main">JESUS CHRIS IS LORD</span>
    </div>

    <div class="details">
      <div class="detail">
        <svg viewBox="0 0 46 46"><circle cx="23" cy="23" r="23" fill="#f3941f"/><rect x="13" y="14" width="20" height="18" rx="2" fill="none" stroke="#fff" stroke-width="2"/><line x1="13" y1="19" x2="33" y2="19" stroke="#fff" stroke-width="2"/><line x1="18" y1="11" x2="18" y2="16" stroke="#fff" stroke-width="2"/><line x1="28" y1="11" x2="28" y2="16" stroke="#fff" stroke-width="2"/></svg>
        <span>Tuesday July 2nd, 2019</span>
      </div>
      <div class="detail">
        <svg viewBox="0 0 46 46"><circle cx="23" cy="23" r="23" fill="#f3941f"/><circle cx="23" cy="24" r="10" fill="none" stroke="#fff" stroke-width="2"/><path d="M23 18v6l4 3" fill="none" stroke="#fff" stroke-width="2"/></svg>
        <span>11:00AM - 7:00PM</span>
      </div>
      <div class="detail">
        <svg viewBox="0 0 46 46"><circle cx="23" cy="23" r="23" fill="#f3941f"/><path d="M23 35s-8-9-8-15a8 8 0 0 1 16 0c0 6-8 15-8 15z" fill="none" stroke="#fff" stroke-width="2"/><circle cx="23" cy="20" r="3" fill="none" stroke="#fff" stroke-width="2"/></svg>
        <span>Belmora Hotel, 4875 Wexley Avenue,<br>Portland, Maine 04102<br>Room: Juniper</span>
      </div>
    </div>

    <div class="footer-rule"></div>
    <div class="footer-brand"><span class="brand-name">TOLVEX</span></div>

    <div class="contact">
      <div class="contact-row">
        <svg viewBox="0 0 24 24"><circle cx="12" cy="12" r="10" fill="none" stroke="#fff" stroke-width="1.5"/><ellipse cx="12" cy="12" rx="4.5" ry="10" fill="none" stroke="#fff" stroke-width="1.5"/><line x1="2" y1="12" x2="22" y2="12" stroke="#fff" stroke-width="1.5"/></svg>
        <span>tolvex.org</span>
        <svg viewBox="0 0 24 24"><path d="M3 9c0-3 4-5 9-5s9 2 9 5l-4 1-1-3H8L7 10z" fill="none" stroke="#fff" stroke-width="1.5"/><rect x="6" y="12" width="12" height="8" rx="1" fill="none" stroke="#fff" stroke-width="1.5"/></svg>
        <span>207 555 3184</span>
      </div>
      <div class="contact-row">
        <svg viewBox="0 0 24 24"><rect x="2" y="5" width="20" height="14" fill="none" stroke="#fff" stroke-width="1.5"/><path d="M2 5l10 8 10-8" fill="none" stroke="#fff" stroke-width="1.5"/></svg>
        <span>contact@brookhavenfold.org</span>
      </div>
    </div>
  </div>
</div>
</body>
</html>
```